Organization and people consulting firm needs a website design

I need a website that promotes and explains the consulting service we will provide. The organization is called Bluefinch Advisory Partners. Our services include organization design, employee experience, change management, and executive coaching. I would like to see a simple clean and professional design, that reflects a modern and forward looking professional services company

Target Market(s)

Mid market and large companies

Industry/Entity Type

Management Consulting

Coding

Coded - Design and coding required

Number of Pages Required

5+ page

Font styles to use
Sans Serif

Colors

Designer to choose colors to be used in the design.

Requirements
Must have
• The following pages: Home, The Way We Work, What We Do, Our Founder, Insights, Contact.
• Search button.
• Hyper links (will be provided with main body text)
• Scrolling website with summaries at top level and links to more detail at lower level (like this website: veltracore.com)
• Company logo (uploaded)
• I have text for each of the pages that I can upload once the basic design is done
Should not have
• No clutter, keep the design clean

```html
<!DOCTYPE html>
<html lang="en">
<head>
<meta charset="utf-8">
<title>Bluefinch Advisory Partners</title>
<link href="https://fonts.googleapis.com/css2?family=Libre+Baskerville:wght@400;700&family=Open+Sans:wght@400;600&display=swap" rel="stylesheet">
<style>
:root{
  --red:#e3233a;
  --dark:#26272b;
  --darker:#1c1d20;
  --ink:#4a4a4a;
  --muted:#8a8a8a;
  --white:#ffffff;
  --line:#d9d9d9;
  --serif:"Libre Baskerville", Georgia, serif;
  --sans:"Open Sans", Arial, sans-serif;
}
*{margin:0;padding:0;box-sizing:border-box}
html,body{width:1200px;height:4091px;overflow:hidden}
body{position:relative;font-family:var(--sans);color:var(--ink);background:var(--white)}
.section{position:absolute;left:0;width:1200px}
.center{text-align:center}
.title{font-family:var(--serif);font-weight:400;font-size:39px;color:#6b6b6b}
.title em{font-style:normal;color:var(--red)}
.lead{font-size:13.5px;line-height:25px;color:var(--muted);width:900px;margin:0 auto}
.btn{display:inline-block;font-family:var(--serif);font-size:15px;padding:13px 36px;border:2px solid #bfbfbf;color:#6b6b6b;text-decoration:none}
.btn.light{border-color:#e5e5e5;color:#fff}

/* hero */
.hero{top:0;height:675px;background:linear-gradient(160deg,#8d8a86 0%,#5f5c5a 45%,#3c3a3a 100%)}
.hero-photo{position:absolute;inset:0;background:radial-gradient(ellipse at 55% 45%,rgba(236,230,222,.55),rgba(40,38,38,.2) 70%)}
.brand{position:absolute;left:96px;top:38px;display:flex;align-items:center;gap:12px;font-family:var(--serif);font-size:22px;color:var(--red)}
.brand-mark{width:26px;height:26px;background:var(--red)}
.search{position:absolute;left:665px;top:28px;display:flex}
.search-field{width:180px;height:30px;background:#fff}
.search-btn{width:58px;height:30px;background:var(--red);display:flex;align-items:center;justify-content:center}
.call{position:absolute;left:918px;top:33px;font-size:15px;color:#fff;display:flex;align-items:center;gap:6px}
.call span{color:var(--red)}
.nav{position:absolute;right:88px;top:74px;display:flex;gap:38px;font-family:var(--serif);font-size:15px;color:#fff}
.hero-title{position:absolute;top:250px;width:100%;text-align:center;font-family:var(--serif);font-size:46px;line-height:55px;color:#fff;letter-spacing:1px}
.hero-title em{font-style:normal;color:var(--red)}
.hero .btn{position:absolute;left:516px;top:442px}
.arrow{position:absolute;top:354px;width:40px;height:40px;border-radius:50%;background:#1d1d1d;display:flex;align-items:center;justify-content:center}

/* way we work */
.way{top:675px;height:400px}
.way .title{margin-top:62px}
.way .lead{margin-top:34px}
.way .btn{margin-top:38px}

/* what we do */
.what{top:1072px;height:762px;background:linear-gradient(180deg,#2c2d31,#1f2023)}
.what .title{margin-top:118px;color:#9a9a9a}
.what .lead{margin-top:28px;color:#e6e6e6;width:860px}
.cards{position:absolute;top:281px;left:87px;display:flex;gap:13px}
.card{width:247px;height:352px;background:#fff;text-align:center}
.card-img{height:167px}
.card h3{font-family:var(--serif);font-weight:400;font-size:16px;color:#555;margin:16px 0 10px}
.card p{font-size:11.5px;line-height:17px;color:#666;padding:0 18px}
.card a{display:block;margin-top:18px;font-size:11px;color:#777;text-decoration:none}

/* founder */
.founder{top:1834px;height:642px}
.founder .title{margin-top:98px}
.founder-photo{position:absolute;left:237px;top:188px;width:260px;height:275px;background:linear-gradient(160deg,#e7ecf0,#b9c3cc)}
.founder-body{position:absolute;left:554px;top:190px;width:410px}
.founder-body h3{font-family:var(--serif);font-weight:400;font-size:23px;color:var(--red)}
.role{font-size:14px;color:#444;margin-top:6px}
.founder-body p{font-size:13.5px;line-height:25px;color:var(--muted);margin-top:32px}
.founder .btn{position:absolute;left:554px;top:493px}

/* insights */
.insights{top:2476px;height:500px;background:linear-gradient(180deg,#2b2c30,#1b1c1f)}
.insights .title{margin-top:120px;color:#9a9a9a}
.insights .lead{margin-top:30px;color:#5f6065;width:960px}
.insights .btn{margin-top:36px;color:#aaa;border-color:#777}

/* contact */
.contact{top:2973px;height:422px;background:linear-gradient(180deg,#3a3b40,#2a2b2f)}
.contact .title{margin-top:120px;color:#fff}
.contact .lead{margin-top:14px;color:#fff;font-weight:600;width:690px;font-size:13px;line-height:26px}
.contact-card{position:absolute;left:87px;top:3237px;width:1026px;height:254px;background:#fff;display:flex;z-index:2;box-shadow:0 2px 10px rgba(0,0,0,.12)}
.contact-item{flex:1;text-align:center;padding-top:62px}
.contact-item+.contact-item{border-left:1px solid #e3e3e3;margin:40px 0}
.contact-item+.contact-item{padding-top:22px}
.contact-item h4{font-family:var(--serif);font-weight:400;font-size:16px;color:#666;margin-top:14px}
.contact-item p{font-size:14px;line-height:26px;color:#8d8d8d}
.map{top:3395px;height:437px;background:linear-gradient(135deg,#ececec,#f3f3f3 55%,#e6e6e6)}

/* footer */
.footer{top:3832px;height:259px;background:#0d0d0e;text-align:center}
.social{display:flex;justify-content:center;gap:10px;margin-top:70px}
.social span{width:36px;height:36px;border-radius:50%}
.foot-nav{margin-top:22px;font-size:12px;color:#bbb}
.foot-nav span{margin:0 20px}
.copy{margin-top:18px;font-size:12px;color:#888}
</style>
</head>
<body>

<header class="section hero">
  <div class="hero-photo" role="img" aria-label="Team of consultants meeting around a table"></div>
  <div class="brand"><span class="brand-mark"></span>Bluefinch Advisory Partners</div>
  <div class="search">
    <div class="search-field"></div>
    <div class="search-btn"><svg width="16" height="16" viewBox="0 0 16 16"><circle cx="6.5" cy="6.5" r="4.5" fill="none" stroke="#fff" stroke-width="2"/><line x1="10" y1="10" x2="14" y2="14" stroke="#fff" stroke-width="2"/></svg></div>
  </div>
  <div class="call"><svg width="14" height="14" viewBox="0 0 24 24"><path fill="#fff" d="M6.6 10.8a15 15 0 0 0 6.6 6.6l2.2-2.2c.3-.3.7-.4 1-.2 1.1.4 2.3.6 3.6.6.6 0 1 .4 1 1V20c0 .6-.4 1-1 1A17 17 0 0 1 3 4c0-.6.4-1 1-1h3.5c.6 0 1 .4 1 1 0 1.3.2 2.5.6 3.6.1.3 0 .7-.2 1z"/></svg>Call: <span>+1-555-014-2290</span></div>
  <nav class="nav"><span>Home</span><span>The Way We Work</span><span>What We Do</span><span>Our Founder</span><span>Insights</span><span>Contact</span></nav>
  <h1 class="hero-title">WELCOME TO<br><em>BLUEFINCH ADVISORY</em><br>PARTNERS</h1>
  <a class="btn light">Learn More</a>
  <div class="arrow" style="left:20px"><svg width="12" height="12" viewBox="0 0 12 12"><path d="M8 1 3 6l5 5" fill="none" stroke="#fff" stroke-width="2"/></svg></div>
  <div class="arrow" style="left:1140px"><svg width="12" height="12" viewBox="0 0 12 12"><path d="M4 1l5 5-5 5" fill="none" stroke="#fff" stroke-width="2"/></svg></div>
  <svg style="position:absolute;left:0;top:615px" width="1200" height="60" viewBox="0 0 1200 60"><polygon points="0,20 1200,0 1200,60 0,60" fill="#fff"/><polygon points="0,20 600,10 0,58" fill="#e3233a"/></svg>
</header>

<section class="section way center">
  <h2 class="title">The Way <em>We Work</em></h2>
  <p class="lead">Sed ut perspiciatis unde omnis iste natus error sit voluptatem accusantium doloremque laudantium, totam rem aperiam, eaque ipsa quae ab illo inventore veritatis et quasi architecto beatae vitae dicta sunt explicabo. Nemo enim ipsam voluptatem quia voluptas sit aspernatur aut odit aut fugit, sed quia consequuntur magni dolores eos qui ratione voluptatem sequi nesciunt. Neque porro quisquam est, qui dolorem ipsum quia dolor sit amet, consectetur, adipisci velit, sed quia non numquam eius modi tempora incidunt ut labore et dolore magnam aliquam quaerat voluptatem.</p>
  <a class="btn">Learn More</a>
</section>

<section class="section what center">
  <svg style="position:absolute;left:0;top:-3px" width="1200" height="40" viewBox="0 0 1200 40"><polygon points="0,0 1200,0 1200,3 0,3" fill="#fff"/><polygon points="700,3 1200,0 1200,34" fill="#e3233a"/></svg>
  <h2 class="title">What <em>We Do</em></h2>
  <p class="lead">Sed ut perspiciatis unde omnis iste natus error sit voluptatem accusantium doloremque laudantium, totam rem aperiam, eaque ipsa quae ab illo inventore veritatis et quasi architecto beatae vitae dicta sunt explicabo.</p>
  <div class="cards">
    <article class="card"><div class="card-img" role="img" aria-label="Planning pieces laid out on a wooden desk" style="background:linear-gradient(135deg,#5a4632,#8a6e4e)"></div><h3>Organisation Design</h3><p>But I must explain to you how all this mistaken idea of denouncing pleasure and praising pain was born and I will give you a complete</p><a>Learn More</a></article>
    <article class="card"><div class="card-img" role="img" aria-label="Group of employees standing together" style="background:linear-gradient(135deg,#c9c9c9,#6e6e72)"></div><h3>Employee Experience</h3><p>But I must explain to you how all this mistaken idea of denouncing pleasure and praising pain was born and I will give you a complete</p><a>Learn More</a></article>
    <article class="card"><div class="card-img" role="img" aria-label="Wooden blocks arranged to show change" style="background:linear-gradient(135deg,#efe7dc,#c8a87c)"></div><h3>Change Management</h3><p>But I must explain to you how all this mistaken idea of denouncing pleasure and praising pain was born and I will give you a complete</p><a>Learn More</a></article>
    <article class="card"><div class="card-img" role="img" aria-label="Executives around a meeting table seen from above" style="background:linear-gradient(135deg,#3e4a5c,#d8dde3)"></div><h3>Executive Coaching</h3><p>But I must explain to you how all this mistaken idea of denouncing pleasure and praising pain was born and I will give you a complete</p><a>Learn More</a></article>
  </div>
</section>

<section class="section founder center">
  <h2 class="title">Our <em>Founder</em></h2>
  <div class="founder-photo" role="img" aria-label="Portrait of the founder"></div>
  <div class="founder-body" style="text-align:left">
    <h3>Marcus L Whitfield</h3>
    <div class="role">Founder</div>
    <p>Sed ut perspiciatis unde omnis iste natus error sit voluptatem accusantium doloremque laudantium, totam rem aperiam, eaque ipsa quae ab illo inventore veritatis et quasi architecto beatae vitae dicta sunt explicabo. Nemo enim ipsam voluptatem quia voluptas sit aspernatur aut odit aut fugit, sed quia consequuntur magni dolores eos qui ratione voluptatem sequi nesciunt. Neque porro quisquam est, qui dolorem ipsum quia dolor sit amet, consectetur,</p>
  </div>
  <a class="btn">More About Marcus</a>
</section>

<section class="section insights center">
  <svg style="position:absolute;left:0;top:-10px" width="1200" height="50" viewBox="0 0 1200 50"><polygon points="0,0 1200,0 1200,10 0,10" fill="#fff"/><polygon points="0,10 1200,0 1200,10" fill="#fff"/><polygon points="850,7 1200,0 1200,38" fill="#e3233a"/></svg>
  <h2 class="title">Insights</h2>
  <p class="lead">Sed ut perspiciatis unde omnis iste natus error sit voluptatem accusantium doloremque laudantium, totam rem aperiam, eaque ipsa quae ab illo inventore veritatis et quasi architecto beatae vitae dicta sunt explicabo. Nemo enim ipsam voluptatem quia voluptas sit aspernatur aut odit aut fugit, sed quia consequuntur magni dolores eos qui ratione voluptatem sequi nesciunt. Neque porro quisquam est, qui dolorem ipsum quia dolor sit amet, consectetur, adipisci velit, sed quia non numquam eius modi tempora incidunt ut labore et dolore magnam aliquam quaerat voluptatem.</p>
  <a class="btn">Learn More</a>
</section>

<section class="section contact center">
  <svg style="position:absolute;left:0;top:-15px" width="1200" height="60" viewBox="0 0 1200 60"><polygon points="0,0 620,40 0,60" fill="#e3233a"/></svg>
  <h2 class="title">Contact us</h2>
  <p class="lead">Lorem Ipsum is simply dummy text of the printing and typesetting industry. Lorem Ipsum has been the industry's standard dummy text ever since the 1500s</p>
</section>

<div class="contact-card">
  <div class="contact-item" style="padding-top:62px">
    <svg width="30" height="40" viewBox="0 0 24 32"><path fill="#e3233a" d="M12 0C5.4 0 0 5.4 0 12c0 9 12 20 12 20s12-11 12-20C24 5.4 18.6 0 12 0zm0 17a5 5 0 1 1 0-10 5 5 0 0 1 0 10z"/></svg>
    <h4>OUR OFFICE</h4>
    <p>48 Alder Crest Road<br>Maple Glen, CT 06512, U.S.A.</p>
  </div>
  <div class="contact-item">
    <svg width="40" height="30" viewBox="0 0 40 30"><rect width="40" height="30" rx="2" fill="#e3233a"/><path d="M2 3l18 14L38 3" fill="none" stroke="#fff" stroke-width="3"/></svg>
    <h4>OUR MAIL</h4>
    <p>info@bluefinchadvisorypartners.com</p>
  </div>
  <div class="contact-item">
    <svg width="36" height="36" viewBox="0 0 24 24"><path fill="#e3233a" d="M6.6 10.8a15 15 0 0 0 6.6 6.6l2.2-2.2c.3-.3.7-.4 1-.2 1.1.4 2.3.6 3.6.6.6 0 1 .4 1 1V20c0 .6-.4 1-1 1A17 17 0 0 1 3 4c0-.6.4-1 1-1h3.5c.6 0 1 .4 1 1 0 1.3.2 2.5.6 3.6.1.3 0 .7-.2 1z"/></svg>
    <h4>OUR PHONE</h4>
    <p>+1-555-014-2290</p>
  </div>
</div>

<div class="section map" role="img" aria-label="Street map showing the office location"></div>

<footer class="section footer">
  <div class="social">
    <span style="background:#3b5998"></span>
    <span style="background:#1da1f2"></span>
    <span style="background:#dd4b39"></span>
    <span style="background:#e62117"></span>
    <span style="background:#c13584"></span>
  </div>
  <div class="foot-nav"><span>Home</span>|<span>The Way We Work</span>|<span>What We Do</span>|<span>Our Founder</span>|<span>Insights</span>|<span>Contact</span></div>
  <div class="copy">Copyright © 2018. Bluefinch Advisory Partners. All rights reserved.</div>
</footer>

</body>
</html>
```